Trabworth Business Cards

We need a business card design for Trabworth Mining.

This is a B2B company that buys and sells large machinery tires within the coal mining industry. The design should the strong, crisp and masculine. I have uploaded the company logo and rough mock-up of what the back of the card should look like. the front of the card should have the same look/feel as the back. I need editable templates for both the front and the back of the card.

Color scheme should be grey/green/black

Contact information to include on the card:
Name: Dale Pembrose
Title: Managing Director
Phone: 555-314-2069
Address: 1187 Welford #3 Dallas, TX 75290
Email: Dale@Trabworth-example.com

I am also opening a contest for letterhead design. If you submit a business card design, please also submit a letterhead design with the same look/feel. The winner of the business card design will also will the letter head and be paid for both.

Target Market(s)

Procurement men/women in the coal mining industry

Industry/Entity Type

Coal Mining

```html
<!DOCTYPE html>
<html lang="en">
<head>
<meta charset="utf-8">
<title>Trabworth Mining Business Cards</title>
<link href="https://fonts.googleapis.com/css2?family=Ubuntu:wght@400;500;700&display=swap" rel="stylesheet">
<style>
  :root {
    --stage: #e8e5e1;
    --card-light: #ffffff;
    --card-dark: #2f3030;
    --green: #6cb33f;
    --grey: #5f6163;
    --ink: #2b2b2b;
    --white: #ffffff;
  }
  * { margin: 0; padding: 0; box-sizing: border-box; }
  html, body {
    width: 1200px; height: 900px; overflow: hidden;
    background: var(--stage);
    font-family: "Ubuntu", sans-serif;
  }
  .stage { position: relative; width: 1200px; height: 900px; }
  .card {
    position: absolute; left: 354px; width: 488px; height: 278px;
    overflow: hidden;
    box-shadow: 0 3px 10px rgba(0,0,0,0.18);
  }
  .card-front { top: 162px; background: var(--card-light); }
  .card-back { top: 472px; background: var(--card-dark); }

  .brand { position: absolute; display: flex; align-items: center; gap: 10px; font-weight: 700; letter-spacing: 0.5px; }
  .brand-square { width: 16px; height: 16px; background: var(--green); flex: none; }
  .card-front .brand { left: 38px; top: 46px; font-size: 26px; color: var(--grey); }
  .card-back .brand { left: 0; right: 0; top: 112px; justify-content: center; font-size: 30px; color: var(--white); }

  .name-tab {
    position: absolute; left: 0; top: 130px; width: 16px; height: 44px;
    background: var(--green); border-radius: 0 6px 6px 0;
  }
  .holder { position: absolute; left: 39px; top: 134px; color: var(--ink); }
  .holder-name { font-size: 16px; line-height: 20px; }
  .holder-title { font-size: 11px; line-height: 16px; text-transform: uppercase; }

  .contact { position: absolute; left: 39px; top: 193px; list-style: none; }
  .contact li { display: flex; align-items: center; gap: 16px; font-size: 13px; line-height: 21px; color: var(--ink); }
  .contact svg { width: 11px; height: 11px; flex: none; }

  .web { position: absolute; left: 0; right: 0; top: 215px; text-align: center; color: var(--white); font-size: 13px; letter-spacing: 0.5px; }
  .bottom-bar {
    position: absolute; left: 107px; bottom: 0; width: 274px; height: 17px;
    background: var(--green); border-radius: 6px 6px 0 0;
  }
</style>
</head>
<body>
<main class="stage">
  <section class="card card-front">
    <div class="brand"><span class="brand-square"></span><span>Trabworth Mining</span></div>
    <div class="name-tab"></div>
    <div class="holder">
      <p class="holder-name">Dale Pembrose</p>
      <p class="holder-title">Managing Director</p>
    </div>
    <ul class="contact">
      <li>
        <svg viewBox="0 0 12 12" aria-hidden="true"><path d="M2 1l2 0 1 3-1.5 1a7 7 0 0 0 3.5 3.5L8 7l3 1v2a1 1 0 0 1-1 1A9 9 0 0 1 1 2a1 1 0 0 1 1-1z" fill="var(--green)"/></svg>
        <span>555-314-2069</span>
      </li>
      <li>
        <svg viewBox="0 0 12 12" aria-hidden="true"><rect x="1" y="3" width="10" height="7" fill="none" stroke="var(--green)" stroke-width="1.6"/><path d="M1 3l5 4 5-4" fill="none" stroke="var(--green)" stroke-width="1.4"/></svg>
        <span>Dale@Trabworth-example.com</span>
      </li>
      <li>
        <svg viewBox="0 0 12 12" aria-hidden="true"><circle cx="6" cy="5" r="3.5" fill="none" stroke="var(--green)" stroke-width="1.8"/><circle cx="6" cy="5" r="1.2" fill="var(--green)"/><path d="M6 8.5v3" stroke="var(--green)" stroke-width="1.6"/></svg>
        <span>1187 Welford #3 Dallas, TX 75290</span>
      </li>
    </ul>
  </section>

  <section class="card card-back">
    <div class="brand"><span class="brand-square"></span><span>Trabworth Mining</span></div>
    <p class="web">www.Trabworth.com</p>
    <div class="bottom-bar"></div>
  </section>
</main>
</body>
</html>
```